Zilata - Sketches from a quiet road

🎨 Design Guidelines
1. Overall Impression

Dignified, spiritual, timeless

Central focus on sand dunes with footsteps as the main motif

Mood: calm, light, spirituality, hope

2. Color Scheme

Background: warm sand tones (beige, golden, brown)

Light source (sun/beam): soft gold/white

Typography: gold or warm yellow, metallic effect preferred (gold foil in print)

Spine and back cover: darker gradient from sand tones to deep blue/black for strong readability

3. Imagery

Front cover: sand dunes with clear footsteps leading towards light/horizon

No figurative depictions of people

Optional: subtle Islamic ornaments or geometric borders as a background accent

4. Typography

Title: “Zīlāta” → large, serif font, elegant, in gold

Subtitle: “Sketches From A Quiet Road” → smaller, clean & modern, also gold/white

Author: Idrīs-Wahīd Salmūn Qāzinī → bottom of the front cover, smaller size

Spine: Title + Arabic word زيلاتة vertically placed, harmonized with the style

5. Back Cover

Short blurb/description (provided by client)

Highlighted keywords in large type: "Courage. Integrity. Faith."

ISBN + barcode at the bottom left

Background: continuation of the sand texture from the front cover (with or without footsteps)

6. Finishing Options (Print)

Gold foil stamping for the title

Matte cover with selective gloss (eg on the light or ornaments)

High-quality, sturdy cover stock

Target Market(s)

Islamic

Font styles to use
Serif

Requirements
Must have
• read the guidelines!
Nice to have
• read the guidelines!
Should not have
• read the guidelines!

```html
<!DOCTYPE html>
<html lang="en">
<head>
<meta charset="utf-8">
<title>Zīlāta – Sketches From A Quiet Road – Cover Wrap</title>
<link rel="stylesheet" href="https://fonts.googleapis.com/css2?family=Noto+Serif:wght@400;600;700&family=Rajdhani:wght@600&family=Cairo:wght@300&display=swap">
<style>
  :root {
    --page-bg: #ffffff;
    --sand-light: #e3cb9c;
    --night: #1a1830;
    --night-deep: #11122a;
    --keyword-gold: #f2dfa4;
    --gold-light: #f7dc6a;
    --gold-rich: #e2b52a;
    --gold-deep: #b8860b;
    --gold-dark: #5e3f08;
    --ivory: #fbf8e9;
    --cream-text: #fdf6e6;
  }
  * { margin: 0; padding: 0; box-sizing: border-box; }
  html, body { width: 1200px; height: 872px; overflow: hidden; background: var(--page-bg); }
  .canvas { position: relative; width: 1200px; height: 872px; }

  .cover-wrap {
    position: absolute; left: 43px; top: 43px; width: 1117px; height: 786px;
    box-shadow: 0 10px 28px rgba(0,0,0,.35);
    overflow: hidden;
  }

  /* Back cover */
  .back-cover {
    position: absolute; left: 0; top: 0; width: 526px; height: 786px;
    background: linear-gradient(180deg, var(--sand-light) 0%, #d7ba86 30%, #b0926a 48%, #6e5a4a 62%, #3b3140 78%, var(--night) 100%);
  }
  .back-ornament {
    position: absolute; left: 24px; top: 8px; width: 478px; height: 290px;
    background: radial-gradient(ellipse 60% 70% at 50% 80%, rgba(255,240,200,.25), rgba(255,240,200,0) 70%);
    border: 1px solid rgba(190,160,110,.25);
    border-bottom: none;
  }
  .back-keywords {
    position: absolute; left: 34px; top: 254px; width: 458px;
    font-family: "Noto Serif", serif; font-weight: 700; font-size: 32px; line-height: 1;
    color: var(--keyword-gold); white-space: nowrap;
  }
  .back-blurb {
    position: absolute; left: 34px; top: 300px; width: 458px;
    font-family: "Noto Serif", serif; font-size: 15px; line-height: 20.1px; letter-spacing: .2px;
    color: var(--cream-text); text-align: justify; text-align-last: center;
  }
  .isbn-box {
    position: absolute; left: 162px; top: 586px; width: 200px; height: 79px;
    background: var(--ivory);
  }

  /* Spine */
  .spine {
    position: absolute; left: 526px; top: 0; width: 65px; height: 786px;
    background: linear-gradient(180deg, var(--sand-light) 0%, #d2b685 30%, #8c7560 55%, #3a3448 78%, var(--night-deep) 100%);
  }
  .spine-title {
    position: absolute; left: 50%; top: 130px;
    transform: translateX(-50%); writing-mode: vertical-rl;
    font-family: "Noto Serif", serif; font-weight: 600; font-size: 40px;
    color: var(--ivory); line-height: 1;
    text-shadow: 0 0 6px rgba(120,90,40,.35);
  }
  .spine-arabic {
    position: absolute; left: 50%; top: 534px;
    transform: translateX(-50%); writing-mode: vertical-rl;
    font-family: "Cairo", sans-serif; font-weight: 300; font-size: 46px; line-height: 1;
    color: var(--gold-rich);
  }

  /* Front cover */
  .front-cover { position: absolute; left: 591px; top: 0; width: 526px; height: 786px; overflow: hidden; }
  .sky-image {
    position: absolute; left: 0; top: 0; width: 100%; height: 380px;
    background:
      radial-gradient(ellipse 40% 42% at 48% 82%, rgba(255,252,232,1) 0%, rgba(255,238,180,.9) 35%, rgba(255,220,140,0) 100%),
      linear-gradient(180deg, #2e2a1e 0%, #5e5236 16%, #a88f5c 34%, #dcc48c 56%, #f2dcaa 80%, #ecc47c 100%);
  }
  .dune-image {
    position: absolute; left: 0; top: 330px; width: 100%; height: 456px;
    background:
      linear-gradient(180deg, rgba(236,196,124,1) 0%, rgba(236,196,124,0) 14%),
      linear-gradient(118deg, #9c5418 0%, #c06f22 30%, #e59b36 52%, #f2b24a 70%, #d98a26 100%);
  }
  .front-frame {
    position: absolute; left: 22px; top: 6px; width: 481px; height: 335px;
    border: 2px solid rgba(230,205,140,.55); border-bottom: none;
  }
  .front-title {
    position: absolute; left: 0; right: 0; top: 196px; text-align: center;
    font-family: "Noto Serif", serif; font-weight: 700; font-size: 132px; line-height: 1;
    background: linear-gradient(180deg, var(--gold-light) 0%, var(--gold-rich) 45%, var(--gold-deep) 100%);
    -webkit-background-clip: text; background-clip: text; color: transparent;
    -webkit-text-stroke: 1.2px var(--gold-dark);
  }
  .front-subtitle {
    position: absolute; left: 0; right: 0; top: 338px; text-align: center;
    font-family: "Rajdhani", sans-serif; font-weight: 600; font-size: 35px; line-height: 1;
    color: #ffffff;
  }
  .front-author {
    position: absolute; left: 0; right: 0; top: 752px; transform: translateY(-50%);
    text-align: center;
    font-family: "Noto Serif", serif; font-size: 28px; line-height: 1;
    color: #ffffff;
  }
</style>
</head>
<body>
<div class="canvas">
  <div class="cover-wrap">

    <section class="back-cover">
      <div class="back-ornament" role="img" aria-label="Faint arched geometric ornament in sand tones"></div>
      <h2 class="back-keywords">COURAGE. INTEGRITY. FAITH</h2>
      <p class="back-blurb">Lorem ipsum dolor sit amet, consectetur adipiscing elit, sed do eiusmod tempor incididunt ut labore et dolore magna aliqua. Quis ipsum suspendisse ultrices gravida. Risus commodo viverra maecenas accumsan lacus vel facilisis. Lorem ipsum dolor sit amet, consectetur adipiscing elit, sed do eiusmod tempor incididunt ut labore et dolore magna aliqua. Quis ipsum suspendisse Risus commodo ultrices gravida. Risus commodo viverra maecenas accumsan lacus vel facilised do ei-usmod sis. sed do eiusmod tempor incididunt ut labore et dolore magna aliqua. Quis ipsum suspendisse ultrices gravida. Risus commodo viverra maecenas accumsan lacus vel facilised do eiusmod sis.</p>
      <div class="isbn-box" aria-label="ISBN area"></div>
    </section>

    <section class="spine">
      <span class="spine-title">Zīlāta</span>
      <span class="spine-arabic" lang="ar" dir="rtl">زيلاتة</span>
    </section>

    <section class="front-cover">
      <div class="sky-image" role="img" aria-label="Glowing sun over a hazy horizon beneath an arched gold geometric lattice ornament"></div>
      <div class="dune-image" role="img" aria-label="Golden rippled sand dunes with a trail of footsteps winding up toward the horizon"></div>
      <div class="front-frame"></div>
      <h1 class="front-title">Zīlāta</h1>
      <p class="front-subtitle">Sketches From A Quiet Road</p>
      <p class="front-author">Idrīs-Wahīd Salmūn Qāzinī</p>
    </section>

  </div>
</div>
</body>
</html>
```